Werbetafel für Immobilienverwaltung
Zielgruppe
Wir sind im Kern eine Immobilienverwaltung, daher richten wir uns an Eigentümer/Investoren/Kapitalanleger. Neben der Verwaltung welche auch durch Hausmeisterservice (Grünarbeiten usw.) erweitert werden kann, bieten wir die Gutachtenerstellung sowie den Vertrieb (Maklertätigkeit in Verkauf sowie Vermietung) an.
Ein großer Vorteil ist unsere Digitale Arbeitsweise (noch keine Selbstverständlichkeit in der Branche).
Aufgabenstellung
Ziel ist es, das Unternehmen unaufdringlich jedoch wirksam und informativ auf einer Werbetafel zu präsentieren.
Maße der Tafel, welche sich im ausgangsbereich eines großen Lebensmittelunternehmens befindet, ist B 320cm x H 120cm.
Die Kundschaft läuft in ca. 1m Entfernung an der Tafel vorbei, sie sollte also von nahem nicht zu überrumpelt wirken.
Unser Logo sowie Telefonnummer sollte iwie untergebracht werden.
Gern auch eigene Ideen umsetzen falls Ihr welche habt.

```html
<!DOCTYPE html>
<html lang="de">
<head>
<meta charset="utf-8">
<title>Werbetafel – Nordhaus Immobilien</title>
<link rel="stylesheet" href="https://fonts.googleapis.com/css2?family=Montserrat:wght@500;700&display=swap">
<style>
  :root {
    --brand-red: #922024;
    --brand-grey: #58595b;
    --line-grey: #9a9a96;
    --backdrop: #f2f2f2;
    --board: #ffffff;
  }
  html, body {
    margin: 0;
    padding: 0;
    width: 1200px;
    height: 960px;
    overflow: hidden;
    background: var(--backdrop);
    font-family: "Montserrat", Arial, sans-serif;
  }
  .billboard {
    position: absolute;
    left: 61px;
    top: 144px;
    width: 1077px;
    height: 673px;
    background: var(--board);
    overflow: hidden;
  }
  .headline {
    position: absolute;
    left: 78px;
    top: 66px;
    margin: 0;
    font-weight: 700;
    font-size: 84px;
    line-height: 93px;
    letter-spacing: -1.5px;
  }
  .headline .line-red { color: var(--brand-red); display: block; }
  .headline .line-grey { color: var(--brand-grey); display: block; }
  .cta {
    position: absolute;
    left: 73px;
    top: 362px;
    margin: 0;
    color: var(--brand-red);
    font-weight: 700;
    font-size: 42px;
    line-height: 1.2;
    letter-spacing: -0.5px;
  }
  .phone {
    position: absolute;
    left: 73px;
    top: 416px;
    margin: 0;
    color: var(--brand-grey);
    font-weight: 700;
    font-size: 90px;
    line-height: 1.2;
    letter-spacing: -1.5px;
  }
  .accent-bar {
    position: absolute;
    left: 0;
    top: 577px;
    width: 655px;
    height: 40px;
    background: var(--brand-red);
  }
  .brand {
    position: absolute;
    left: 682px;
    top: 556px;
    width: 360px;
  }
  .brand-name {
    display: flex;
    align-items: center;
    gap: 10px;
    color: var(--brand-red);
    font-weight: 700;
    font-size: 28px;
    line-height: 1;
    white-space: nowrap;
  }
  .brand-square {
    width: 22px;
    height: 22px;
    background: var(--brand-red);
    flex: none;
  }
  .brand-rule {
    margin-top: 10px;
    height: 1px;
    background: var(--line-grey);
  }
  .brand-tagline {
    margin-top: 6px;
    padding-left: 76px;
    color: var(--brand-grey);
    font-weight: 500;
    font-size: 11.5px;
    letter-spacing: 0.6px;
    white-space: nowrap;
  }
</style>
</head>
<body>
  <main class="billboard">
    <h1 class="headline">
      <span class="line-red">Ihre Immobilie -</span>
      <span class="line-grey">unser Know-Haus</span>
    </h1>
    <p class="cta">Jetzt anmelden</p>
    <p class="phone">0391 480 27 63</p>
    <div class="accent-bar"></div>
    <div class="brand">
      <div class="brand-name"><span class="brand-square"></span>Nordhaus Immobilien</div>
      <div class="brand-rule"></div>
      <div class="brand-tagline">WIR KÜMMERN UNS UM IHR ZUHAUSE</div>
    </div>
  </main>
</body>
</html>
```